National Sales - Pick Up Truck Dealer

We need a logo design for a new vehicle dealership based in Sydney, Australia. The business name is Coastal Iron Haulers Motor Co. We will be selling American 'trucks/pick up trucks' like KRV, Torvan, Blaxer, Morrow T420, Kenzo Raptors, Morrow T640 and the likes.

These vehicles are a luxury option and we would like the logo to be strong, luxurious and masculine.Colours will be black and red or black and blue with the option of grey and white.

Target Market(s)

Men

Industry/Entity Type

Car Dealer

Contact Information for Business Card

Dennis Harlowe
Managing Director
0412 639 274
den@qelvtrk.com.au

Level 5, Brindle Parkway
17 Pemberly Lane
Baulkham Hills
NSW
Australia
Licence No: MD493152

Back of the card

qelvtrk.com.au

Font styles to use
Sans Serif

Colors

Designer to choose colors to be used in the design.

Requirements
Must have
• The company logo that is in the attachments, you can choose from the three which one you would like to work with. Must have vehicle images ....Please look at the attachments as they show examples of what we like and also provides potential images. If you choose to put an image on the front even if it is just the front of the vehicle can you please use the Black KRV Sorrento. Must have all details from the business card details section front and back
Nice to have
• N/A
Should not have
• No cars or standard trucks, please refer to the attached images to understand the product . Should not have any new logos or branding. No other colours besides what is in the logo you choose.

```html
<!DOCTYPE html>
<html lang="en">
<head>
<meta charset="utf-8">
<title>Coastal Iron Haulers Motor Co – Business Card</title>
<link rel="stylesheet" href="https://fonts.googleapis.com/css2?family=Roboto+Condensed:wght@400;700&family=Roboto:wght@400&display=swap">
<style>
  :root {
    --stage: #e9e6e2;
    --paper: #f4f4f4;
    --ink: #222326;
    --black: #0b0c0d;
    --carbon: #1d1f22;
    --white: #ffffff;
    --accent-blue: #3ea3dc;
    --truck-blue: #24356e;
  }
  * { margin: 0; padding: 0; box-sizing: border-box; }
  html, body { width: 1200px; height: 960px; overflow: hidden; }
  body {
    position: relative;
    background: var(--stage);
    font-family: "Roboto", sans-serif;
  }
  .card {
    position: absolute;
    width: 600px;
    height: 343px;
    box-shadow: 0 3px 8px rgba(0,0,0,0.35);
    overflow: hidden;
  }
  .card-front { left: 314px; top: 113px; }
  .card-back { left: 311px; top: 472px; }

  /* front */
  .front-top {
    position: absolute; left: 0; top: 0;
    width: 600px; height: 223px;
    background: var(--paper);
  }
  .brand-name {
    font-family: "Roboto Condensed", sans-serif;
    font-weight: 700;
    text-transform: uppercase;
    text-align: center;
    line-height: 1.05;
  }
  .front-top .brand-name {
    position: absolute; left: 0; right: 0; top: 48px;
    font-size: 34px;
    color: var(--ink);
  }
  .truck-photo {
    position: absolute; left: 463px; top: 176px;
    width: 94px; height: 44px;
    border-radius: 8px 14px 4px 4px;
    background: linear-gradient(180deg, #3a4c8a 0%, var(--truck-blue) 55%, #141a30 100%);
  }
  .front-bottom {
    position: absolute; left: 0; top: 223px;
    width: 600px; height: 120px;
    background: radial-gradient(ellipse at 50% 70%, var(--carbon) 0%, var(--black) 75%);
    color: var(--white);
  }
  .contact-person { position: absolute; left: 41px; top: 14px; }
  .person-name {
    font-family: "Roboto Condensed", sans-serif;
    font-weight: 700; font-size: 21px; text-transform: uppercase;
    line-height: 24px;
  }
  .person-role {
    font-family: "Roboto Condensed", sans-serif;
    font-size: 16px; text-transform: uppercase; line-height: 22px;
  }
  .contact-line {
    display: flex; align-items: center; gap: 9px;
    font-size: 14px; line-height: 18px;
  }
  .contact-line.phone { margin-top: 3px; }
  .contact-line svg { width: 13px; height: 13px; flex: none; }
  .address {
    position: absolute; right: 26px; top: 14px;
    text-align: right; font-size: 14px; line-height: 18px;
    font-style: normal;
  }

  /* back */
  .card-back {
    background: radial-gradient(ellipse at 50% 40%, #2b2d31 0%, #141517 55%, var(--black) 100%);
  }
  .back-texture { position: absolute; inset: 0; }
  .card-back .brand-name {
    position: absolute; left: 0; right: 0; top: 118px;
    font-size: 40px; color: var(--white);
  }
  .website {
    position: absolute; left: 0; right: 0; top: 276px;
    text-align: center; font-size: 19px; letter-spacing: 1px;
    color: var(--accent-blue);
  }
</style>
</head>
<body>

<section class="card card-front">
  <div class="front-top">
    <div class="brand-name">Coastal Iron Haulers<br>Motor Co</div>
    <div class="truck-photo" role="img" aria-label="Black KRV Sorrento pick-up truck"></div>
  </div>
  <div class="front-bottom">
    <div class="contact-person">
      <div class="person-name">Dennis Harlowe</div>
      <div class="person-role">Managing Director</div>
      <div class="contact-line phone">
        <svg viewBox="0 0 24 24" aria-hidden="true"><path fill="#fff" d="M6.6 10.8a15.1 15.1 0 0 0 6.6 6.6l2.2-2.2c.3-.3.7-.4 1-.2 1.1.4 2.3.6 3.6.6.6 0 1 .4 1 1V20c0 .6-.4 1-1 1C10.6 21 3 13.4 3 4c0-.6.4-1 1-1h3.5c.6 0 1 .4 1 1 0 1.3.2 2.5.6 3.6.1.3 0 .7-.2 1z"/></svg>
        <span>0412 639 274</span>
      </div>
      <div class="contact-line email">
        <svg viewBox="0 0 24 24" aria-hidden="true"><path fill="#fff" d="M3 5h18c.6 0 1 .4 1 1v12c0 .6-.4 1-1 1H3c-.6 0-1-.4-1-1V6c0-.6.4-1 1-1zm1 2.2V17h16V7.2l-8 5.3-8-5.3zM5.6 7 12 11.2 18.4 7H5.6z"/></svg>
        <span>den@qelvtrk.com.au</span>
      </div>
    </div>
    <address class="address">
      Level 5, Brindle Parkway<br>
      17 Pemberly Lane<br>
      Baulkham Hills<br>
      NSW, Australia<br>
      Licence No: MD493152
    </address>
  </div>
</section>

<section class="card card-back">
  <div class="back-texture" role="img" aria-label="Dark carbon hexagon texture"></div>
  <div class="brand-name">Coastal Iron Haulers<br>Motor Co</div>
  <div class="website">qelvtrk.com.au</div>
</section>

</body>
</html>
```